Healthy Meal Delivery Website Needs to be updated, current, fresh and modern

Hi there,

The current website i have is super old and outdated.

I would like a beautiful modern site that has all the same content as the previous except with a a new, modern and trustworthy feel.

The current website is https://tovalplatefresh.com/

Target Market(s)

Health Conscious Young Professionals

Industry/Entity Type

Food Service

Font styles to use
Sans Serif

Requirements
Must have
• Modern Trustworthy feel
Should not have
• Anything out dated or cheesy or scammy

```html
<!DOCTYPE html>
<html lang="en">
<head>
<meta charset="utf-8">
<title>Toval Plate Fresh – Diet Meal Delivery</title>
<link href="https://fonts.googleapis.com/css2?family=Roboto:wght@400;500;700&family=Roboto+Condensed:wght@400;700&family=PT+Serif:wght@400;700&display=swap" rel="stylesheet">
<style>
:root{
  --blue:#1c9bd7;
  --yellow:#ece51c;
  --ink:#1d1d1d;
  --text:#444;
  --muted:#777;
  --light:#f1f1f1;
  --black:#0c0c0c;
  --white:#fff;
}
*{margin:0;padding:0;box-sizing:border-box}
html,body{width:1200px;height:4128px;overflow:hidden}
body{font-family:"Roboto",Arial,sans-serif;color:var(--text);background:var(--white);position:relative}
.abs{position:absolute}
.btn{position:absolute;background:var(--yellow);color:#2a6e9c;font-family:"PT Serif",Georgia,serif;font-weight:700;font-size:17px;display:flex;align-items:center;justify-content:center;border-radius:4px;box-shadow:0 2px 4px rgba(0,0,0,.2)}
.ph{position:absolute}

/* top bar & header */
.topbar{left:0;top:0;width:1200px;height:33px;background:var(--black);color:#ddd;font-size:14px}
.topbar .items{position:absolute;right:70px;top:0;height:33px;display:flex;align-items:center;gap:26px}
.topbar .phone{background:var(--blue);color:#fff;font-weight:700;padding:0 16px;height:33px;display:flex;align-items:center;font-size:17px}
.header{left:0;top:33px;width:1200px;height:72px;background:#fff}
.brand{position:absolute;left:105px;top:18px;display:flex;align-items:center;gap:10px}
.brand .dot{width:34px;height:34px;border-radius:50%;background:var(--yellow)}
.brand span{font-family:"Roboto",sans-serif;font-weight:700;font-size:22px;color:var(--blue)}
.nav{position:absolute;right:70px;top:30px;display:flex;gap:38px;font-size:15px;color:#555}
.nav .active{color:var(--blue);border-top:2px solid var(--blue);padding-top:4px;margin-top:-6px}

/* hero */
.hero{left:0;top:105px;width:1200px;height:511px;background:linear-gradient(90deg,#e9ecec 0%,#f4f2ee 45%,#d8d4cf 100%)}
.hero .food{left:0;top:0;width:560px;height:420px;background:radial-gradient(ellipse at 40% 50%,#b9d68c,#e8e3d6 70%)}
.hero .figure{left:820px;top:0;width:300px;height:426px;background:linear-gradient(180deg,#c89a80,#e6c5b0)}
.hero .arrow{top:215px;width:28px;height:28px;background:rgba(0,0,0,.6)}
.hero .caption{left:0;top:426px;width:1200px;height:85px;background:rgba(40,40,40,.78);color:#fff;font-family:"Roboto Condensed",sans-serif;font-size:27px;line-height:38px;text-align:center;padding-top:6px}

/* intro */
.intro-title{left:0;top:662px;width:1200px;text-align:center;font-family:"Roboto Condensed",sans-serif;font-weight:700;font-size:28px;color:var(--ink)}
.rule{position:absolute;height:3px;width:70px;background:var(--blue)}
.intro-text{left:0;top:735px;width:1200px;text-align:center;font-size:17px;line-height:28px;color:#555}
.feature{position:absolute;top:822px;width:230px;text-align:center}
.feature .circ{width:116px;height:116px;border-radius:50%;margin:0 auto;display:flex;align-items:center;justify-content:center;border:5px solid #ddd}
.feature h4{margin-top:32px;font-size:15px;font-weight:700;color:var(--ink);letter-spacing:.5px}
.feature p{margin-top:8px;font-size:12px;line-height:17px;color:#555}

/* what is */
.whatis{left:0;top:1203px;width:1200px;height:352px;background:var(--blue)}
.whatis .photo{left:105px;top:52px;width:341px;height:237px;background:linear-gradient(135deg,#f0ece4,#c9b89e);border:4px solid #fff}
.whatis h2{left:462px;top:54px;font-family:"PT Serif",serif;font-size:38px;font-weight:400;color:#fff}
.whatis p{left:462px;top:122px;width:640px;font-family:"PT Serif",serif;font-size:15px;line-height:22px;color:#fff}

/* plan */
.plan-fig{left:0;top:1624px;width:325px;height:624px;background:linear-gradient(180deg,#d9b49a,#e8cf6a 45%,#d9b49a)}
.plan-food{left:325px;top:1962px;width:225px;height:143px;background:radial-gradient(ellipse,#b6c86e,#f3efe3 70%)}
.plan-title{left:0;top:1604px;width:1200px;text-align:center;font-family:"Roboto Condensed",sans-serif;font-weight:700;font-size:36px;color:var(--ink)}
.plan-sub{left:0;top:1680px;width:1200px;text-align:center;font-family:"PT Serif",serif;font-size:17px;color:#333}
.col{position:absolute;font-family:"PT Serif",serif;width:230px}
.col .num{font-family:"Roboto",sans-serif;font-size:48px;color:#d6d6d6;line-height:40px}
.col h5{margin-top:18px;font-size:14px;font-weight:700;color:var(--blue);letter-spacing:.5px}
.col p{margin-top:10px;font-size:15px;line-height:21px;color:#333}

/* testimonials */
.testi{left:0;top:2248px;width:1200px;height:427px;background:radial-gradient(ellipse at 50% 50%,#6a4a38,#2a1f1a 75%)}
.testi h3{position:absolute;left:0;top:100px;width:1200px;text-align:center;font-family:"Roboto",sans-serif;font-weight:400;font-size:30px;color:#fff}
.testi .quote{position:absolute;left:180px;top:182px;width:840px;text-align:center;font-style:italic;font-size:15px;line-height:23px;color:#eee}
.testi .name{position:absolute;left:0;top:295px;width:1200px;text-align:center;font-size:15px;color:#ccc}
.dots{position:absolute;left:570px;top:328px;display:flex;gap:6px}
.dots i{width:8px;height:8px;border-radius:50%;background:#888}
.dots i:first-child{background:var(--yellow)}

/* menu */
.menu-title{left:0;top:2776px;width:1200px;text-align:center;font-family:"Roboto Condensed",sans-serif;font-weight:700;font-size:34px;color:var(--ink)}
.menu-text{left:0;top:2858px;width:1200px;text-align:center;font-size:17px;line-height:27px;color:#444}
.card{position:absolute;top:2964px;width:231px;height:283px;background:#fff;box-shadow:0 2px 10px rgba(0,0,0,.18)}
.card .img{width:231px;height:168px}
.card h6{margin-top:14px;text-align:center;font-size:16px;font-weight:400;color:var(--ink)}
.card p{margin-top:8px;text-align:center;font-size:12px;line-height:16px;color:#666;padding:0 16px}
.card .tab{position:absolute;left:95px;bottom:-2px;width:40px;height:20px;border-radius:20px 20px 0 0;background:#222}
.card.sel h6{color:var(--blue)}
.card.sel{border-bottom:4px solid var(--blue)}
.card.sel .tab{background:var(--blue)}

/* real foods */
.real{left:0;top:3404px;width:1200px;height:353px;background:var(--light)}
.real h3{position:absolute;left:105px;top:56px;width:560px;font-family:"PT Serif",serif;font-size:24px;line-height:32px;color:var(--ink)}
.real p{position:absolute;left:105px;top:150px;width:590px;font-family:"PT Serif",serif;font-size:15px;line-height:22px;color:#333}
.real .photo{left:760px;top:58px;width:346px;height:231px;background:linear-gradient(135deg,#e0b080,#7aa24e)}

/* footer */
.footer{left:0;top:3757px;width:1200px;height:321px;background:var(--black);color:#ccc}
.footer h4{position:absolute;top:52px;font-size:18px;font-weight:400;color:#fff}
.links{position:absolute;left:122px;top:104px;font-size:14px;line-height:33px}
.links li{list-style:none;position:relative}
.links li::before{content:"";position:absolute;left:-14px;top:15px;width:5px;height:5px;background:var(--blue)}
.fdiv{position:absolute;top:52px;width:1px;height:230px;background:#333}
.field{position:absolute;left:597px;width:238px;background:#fff;color:#333;font-size:12px;padding:6px 8px}
.submit{position:absolute;left:597px;top:250px;width:112px;height:34px;background:var(--blue);color:#fff;font-size:16px;display:flex;align-items:center;justify-content:center}
.social{position:absolute;left:895px;top:108px;display:flex;gap:8px}
.social i{width:34px;height:34px;border-radius:50%;background:var(--blue)}
.fbrand{position:absolute;left:895px;top:168px;display:flex;align-items:center;gap:8px}
.fbrand i{width:26px;height:26px;border-radius:50%;background:var(--yellow)}
.fbrand span{font-weight:700;font-size:17px;color:var(--blue)}
.copy{left:0;top:4078px;width:1200px;height:50px;background:var(--blue);color:#fff;font-size:13px;display:flex;align-items:center;justify-content:center}
</style>
</head>
<body>

<div class="abs topbar">
  <div class="items">
    <span>✉ sales@tovalplatefresh.com</span>
    <span class="phone">☎ 416.555.0192</span>
    <span>Login</span>
    <span>Signup</span>
  </div>
</div>

<header class="abs header">
  <div class="brand"><i class="dot"></i><span>Toval Plate Fresh</span></div>
  <nav class="nav">
    <span class="active">Home</span><span>Meal Plans</span><span>Menu</span><span>Pricing</span><span>About</span><span>Press</span><span>Contact Us</span>
  </nav>
</header>

<section class="abs hero">
  <div class="ph food" role="img" aria-label="Plate of fresh lettuce wraps with dipping sauce"></div>
  <div class="ph figure" role="img" aria-label="Fit woman in white sports top holding a bathroom scale"></div>
  <svg class="abs arrow" style="left:8px" viewBox="0 0 28 28"><path d="M17 8l-6 6 6 6" stroke="#fff" stroke-width="2.5" fill="none"/></svg>
  <svg class="abs arrow" style="right:8px" viewBox="0 0 28 28"><path d="M11 8l6 6-6 6" stroke="#fff" stroke-width="2.5" fill="none"/></svg>
  <div class="abs caption">Toronto based diet delivery company that has helped thousands of Canadians slim down and<br>achieve their desired weight loss goals</div>
</section>

<h2 class="abs intro-title">The Toval Plan Delivers Diet Meals To Your Door In Toronto, Gta And Montreal</h2>
<div class="rule" style="left:565px;top:712px"></div>
<p class="abs intro-text">Our fresh and delicious diet meals and snacks are made with only the best natural ingredients that nourish your body.<br>Why not let us prepare your meals while you lose the weight?</p>

<div class="feature" style="left:104px">
  <div class="circ" style="background:var(--yellow);border-color:#f5f2b0"><svg width="50" height="46" viewBox="0 0 50 46"><path d="M25 44C6 30 2 20 2 13A11 11 0 0 1 25 8a11 11 0 0 1 23 5c0 7-4 17-23 31z" fill="#1c9bd7"/><path d="M20 23h10M25 18v10" stroke="#fff" stroke-width="3"/></svg></div>
  <h4>HEALTHY</h4>
  <p>The Toval Plan is a great way to ensure you are eating all the nutrients you need, and nothing your body doesn't need.</p>
</div>
<div class="feature" style="left:368px">
  <div class="circ" style="background:#2a2a2a;border-color:#ddd"><svg width="44" height="44" viewBox="0 0 44 44" fill="none" stroke="#fff" stroke-width="2.5"><rect x="6" y="6" width="18" height="18" rx="3"/><path d="M22 22l12 12M22 22v10M22 22h10"/></svg></div>
  <h4>CHOICE</h4>
  <p>You can choose your own meals from over 100 tasty entrees, desserts &amp; snack foods. You can choose your meals online.</p>
</div>
<div class="feature" style="left:632px">
  <div class="circ" style="background:#2a2a2a;border-color:#ddd"><svg width="50" height="34" viewBox="0 0 50 34"><path d="M4 14h42a21 18 0 0 1-42 0z" fill="#fff"/><circle cx="18" cy="9" r="4" fill="#fff"/><circle cx="27" cy="7" r="4" fill="#fff"/><circle cx="35" cy="10" r="3" fill="#fff"/></svg></div>
  <h4>FRESH</h4>
  <p>All of our meals are real food, freshly prepared by our in-house expert chefs.</p>
</div>
<div class="feature" style="left:882px">
  <div class="circ" style="background:#2a2a2a;border-color:#ddd"><svg width="50" height="40" viewBox="0 0 50 40" fill="#fff"><rect x="4" y="8" width="26" height="20"/><path d="M30 14h9l7 8v6H30z"/><circle cx="12" cy="31" r="5"/><circle cx="38" cy="31" r="5"/></svg></div>
  <h4>CUSTOMIZED</h4>
  <p>Your meals will be delivered fresh to your door, customized for your unique body type and level of activity.</p>
</div>
<div class="btn" style="left:517px;top:1095px;width:150px;height:47px">Get Started</div>

<section class="abs whatis">
  <div class="ph photo" role="img" aria-label="Overhead view of many prepared healthy meals on a table"></div>
  <h2 class="abs">What is Toval?</h2>
  <p class="abs">Toval is the Toronto &amp; Montreal Diet Delivery program based on the Toval Plan™, healthy carbs and the right fats.<br><br>We provide you with 3 fresh meals, 2 snacks &amp; a dessert delivered to your door before 6am.<br>Try our Toval Plan™ delivery plan and start Toval weight loss now!</p>
  <div class="btn" style="left:462px;top:247px;width:260px;height:44px">Try our Toval Plan™ Today</div>
</section>

<div class="ph plan-fig" role="img" aria-label="Slim woman in yellow top measuring her waist with a tape"></div>
<h2 class="abs plan-title">The Toval Plan</h2>
<div class="rule" style="left:565px;top:1660px"></div>
<p class="abs plan-sub">Real foods designed by nature prepared by Toval.</p>
<div class="col" style="left:332px;top:1745px"><div class="num">01</div><h5>WHAT YOU GET</h5><p>Toval Diet Delivery provides you with 3 fresh daily meals and 3 snacks delivered to your doorstep before 6am.</p></div>
<div class="col" style="left:612px;top:1745px"><div class="num">02</div><h5>SELECTION</h5><p>Choose your meals from over 100 delicious entrees, snacks &amp; desserts.</p></div>
<div class="col" style="left:848px;top:1745px"><div class="num">03</div><h5>LUXURY</h5><p>Enjoy the luxury of having your own personal chef and nutritionist prepare Toval Diet meals for you.</p></div>
<div class="ph plan-food" role="img" aria-label="Bowl of guacamole with tortilla chips"></div>
<div class="col" style="left:615px;top:1978px"><h5>WHAT IS PHASE 1?</h5><p>Phase 1 is the stricter phase that eliminates bad carbs and processed foods; no sugar, candy, pasta or bread.</p></div>
<div class="col" style="left:848px;top:1978px"><h5>WHAT IS PHASE 2?</h5><p>Phase 2 reintroduces certain healthy carbs into your diet - whole grains, rice and potatoes, providing you with a greater variety of meals.</p></div>
<div class="btn" style="left:470px;top:2144px;width:258px;height:44px">Try our Toval Plan™ Today</div>

<section class="abs testi" role="img" aria-label="Dimmed close-up photo of a pasta dish behind client testimonials">
  <h3>Clients Testimonials</h3>
  <p class="quote">“ Lorem ipsum dolor sit amet, consectetuer adipiscing elit, sed diam nonummy nibh euismod tincidunt ut laoreet dolore magna aliquam erat volutpat. Ut wisi enim ad minim veniam, quis nostrud exerci tation ullamcorper suscipit lobortis nisl ut aliquip ex ea commodo consequat. ”</p>
  <p class="name">Mr. Lorem Ipsum</p>
  <div class="dots"><i></i><i></i><i></i><i></i></div>
</section>

<h2 class="abs menu-title">Select From Over 100 Menu Items</h2>
<div class="rule" style="left:565px;top:2830px"></div>
<p class="abs menu-text">You can choose your own meals from over 100 tasty entrees, desserts and snack foods.<br>You can choose your meals online, or we can select your meals for you.</p>

<div class="card sel" style="left:105px"><div class="img" role="img" aria-label="Cobb lettuce wraps" style="background:linear-gradient(135deg,#cfe3a8,#8fb45c)"></div><h6>Snacks</h6><p>Cobb Lettuce Wrap</p><i class="tab"></i></div>
<div class="card" style="left:358px"><div class="img" role="img" aria-label="Scrambled eggs with smoked salmon" style="background:linear-gradient(135deg,#f6d24a,#e59a3a)"></div><h6>Breakfast</h6><p>Scrambled Eggs With Dill &amp; Smoked Salmon</p><i class="tab"></i></div>
<div class="card" style="left:622px"><div class="img" role="img" aria-label="Roasted beet and walnut salad" style="background:linear-gradient(135deg,#8a3a3a,#6f8a3a)"></div><h6>Lunch</h6><p>Roasted Beet Walnut And Goat Cheese Salad</p><i class="tab"></i></div>
<div class="card" style="left:875px"><div class="img" role="img" aria-label="Grilled salmon steak over collard greens" style="background:linear-gradient(135deg,#e0875a,#3e5a2a)"></div><h6>Dinner</h6><p>Grilled Salmon Steak With Baked Parsnip Over Collard Greens</p><i class="tab"></i></div>
<div class="btn" style="left:470px;top:3297px;width:258px;height:47px">Try our Toval Plan™ Today</div>

<section class="abs real">
  <h3>The Toval Plan Is Based On Real Foods Made With Fresh And Natural Ingredients.</h3>
  <p>It's about eating the foods you love and emphasizing the ones that nourish your body; generous portions of fresh fruit, vegetables, meat, fish, nuts and seeds, with smaller servings of grains and dairy.</p>
  <div class="ph photo" role="img" aria-label="Smiling woman eating a fresh salad beside a table of healthy dishes"></div>
  <div class="btn" style="left:105px;top:242px;width:192px;height:44px">Customer Login</div>
  <div class="btn" style="left:312px;top:242px;width:160px;height:44px">SignUp Now</div>
</section>

<footer class="abs footer">
  <h4 style="left:110px">Quick Links</h4>
  <ul class="links"><li>Home</li><li>Meal Plans</li><li>Menu</li><li>Pricing</li><li>About</li><li>Press</li></ul>
  <div class="fdiv" style="left:272px"></div>
  <h4 style="left:295px">Contact Details</h4>
  <svg class="abs" style="left:290px;top:108px" width="22" height="22" viewBox="0 0 22 22"><circle cx="11" cy="11" r="11" fill="#1c9bd7"/><path d="M11 5a4 4 0 0 0-4 4c0 3 4 8 4 8s4-5 4-8a4 4 0 0 0-4-4z" fill="#fff"/></svg>
  <p class="abs" style="left:322px;top:106px;font-size:14px;line-height:22px">Toronto<br>416-555-0192</p>
  <svg class="abs" style="left:290px;top:162px" width="22" height="22" viewBox="0 0 22 22"><circle cx="11" cy="11" r="11" fill="#1c9bd7"/><rect x="5" y="7" width="12" height="8" fill="#fff"/></svg>
  <p class="abs" style="left:322px;top:160px;font-size:14px;line-height:22px">Email<br>sales@tovalplatefresh.com</p>
  <p class="abs" style="left:295px;top:222px;font-size:11px;line-height:15px;color:#999">1.4k people follow our updates.<br>Sign up to see new menus.</p>
  <div class="fdiv" style="left:580px"></div>
  <h4 style="left:600px">Quick Inquiry</h4>
  <div class="field" style="top:108px;height:30px">Name</div>
  <div class="field" style="top:144px;height:30px">Email</div>
  <div class="field" style="top:180px;height:64px">Message</div>
  <div class="submit">Submit →</div>
  <div class="fdiv" style="left:868px"></div>
  <h4 style="left:895px">Follow Us</h4>
  <div class="social"><i></i><i></i><i></i><i></i></div>
  <div class="fbrand"><i></i><span>Toval Plate Fresh</span></div>
</footer>
<div class="abs copy">Copyright © 2018 TovalPlateFresh. All Rights Reserved.</div>

</body>
</html>
```